Website for a Psychologist in Private Practice

I need a cool web design for my website: www.drkalvoric.com. I would like it to look professional. Keep all the current content and add: Space for video; radio spots (see Silver Cedar Tunes Logo below for those); Quick Inquiry; Friendora link; 5 star rating on Rivo; a map; reviews from former patients. I am open to suggestions.

Target Market(s)

Those seeking individual and marital counseling.

Industry/Entity Type

Mental Health

Number of Pages Required

1 page

Font styles to use
Sans Serif
Other font styles liked:
• I'm open but no hard to read script

Requirements
Must have
• All the content on my home page with link for video and radio spots. List services and degrees and expertices (pics not necessary).
Nice to have
• A video of me and radio conversations (logo of Silver Cedar Tunes radio attached).
Should not have
• Cartoons, comedy, etc.... I don't need pictures of services (marital, depression, etc...) Just list those.

```html
<!DOCTYPE html>
<html lang="en">
<head>
<meta charset="utf-8">
<title>Dr. Mira L. Kalvoric – Psychologist</title>
<link href="https://fonts.googleapis.com/css2?family=Barlow+Semi+Condensed:wght@400;500;600&family=Raleway:wght@500&family=Arimo:ital,wght@0,400;0,700;1,400;1,700&display=swap" rel="stylesheet">
<style>
:root{
  --blue:#1d86c6;
  --blue-dark:#1670a8;
  --header:rgba(70,90,110,.9);
  --teal-panel:rgba(20,80,90,.35);
  --dark-panel:rgba(30,45,50,.55);
  --gray-panel:rgba(95,100,100,.55);
  --reviews:rgba(60,60,60,.8);
  --footer:#2b2a28;
  --white:#fff;
  --line:#cfd8da;
}
*{margin:0;padding:0;box-sizing:border-box}
html,body{width:783px;height:1200px;overflow:hidden}
body{font-family:"Barlow Semi Condensed",sans-serif;color:var(--white);position:relative}
.scene{position:absolute;inset:0;background:linear-gradient(180deg,#6b8fb0 0%,#c9d9e6 14%,#3fa9b8 26%,#1d8ea0 45%,#5d9aa0 62%,#8f8778 78%,#c6b396 100%)}
.page{position:absolute;left:86px;top:0;width:612px;height:1200px}
.header{position:absolute;top:0;left:0;width:612px;height:62px;background:var(--header)}
.brand{position:absolute;left:9px;top:20px;font-size:26px;font-weight:500;letter-spacing:.2px;white-space:nowrap}
.share{position:absolute;left:375px;top:33px;width:61px;height:20px;background:#3d5f9a;font-size:10px;display:flex;align-items:center;justify-content:center;gap:5px;white-space:nowrap}
.share i{width:9px;height:9px;background:#fff;display:inline-block}
.rating{position:absolute;left:440px;top:12px;width:42px;height:42px;background:#c3231e;border-radius:6px;font-size:12px;font-weight:600;display:flex;align-items:center;justify-content:center}
.call{position:absolute;left:494px;top:19px;display:flex;gap:6px;align-items:center;white-space:nowrap}
.call svg{width:20px;height:20px;flex:none}
.call small{display:block;font-size:11px}
.call b{display:block;font-family:Arimo,sans-serif;font-size:14.5px;font-weight:400}
.nav{position:absolute;top:62px;left:0;width:612px;height:28px;background:var(--blue);display:flex;font-size:11.5px;white-space:nowrap}
.nav a{color:#fff;text-decoration:none;padding:0 10px;line-height:28px;border-right:1px solid var(--blue-dark)}
.nav a.active{color:#111}
.follow{position:absolute;right:6px;top:7px;font-size:8px;display:flex;align-items:center;gap:5px;white-space:nowrap}
.follow span.net{display:flex;align-items:center;gap:2px}
.follow i{width:13px;height:13px;border-radius:50%;background:#3d5f9a;display:inline-block}
.follow i.chirp{background:#29a3e0}
.hero{position:absolute;top:90px;left:0;width:612px;height:287px;background:linear-gradient(180deg,#5c7590 0%,#d4a869 30%,#f3c45a 38%,#a56f26 50%,#c99131 70%,#7a5114 100%)}
.hero h1{position:absolute;top:122px;width:100%;text-align:center;font-family:Raleway,sans-serif;font-weight:500;font-size:17.5px;line-height:23px;text-shadow:0 1px 2px rgba(0,0,0,.5)}
.arrow{position:absolute;top:130px;width:29px;height:24px;background:rgba(255,255,255,.8);display:flex;align-items:center;justify-content:center}
.arrow.prev{left:0}.arrow.next{right:0}
.about{position:absolute;top:377px;left:0;width:612px;height:207px;background:var(--teal-panel)}
h2{font-weight:500;font-size:16px;line-height:16px}
.title-line{height:2px;background:var(--line);position:relative}
.title-line::before{content:"";position:absolute;left:0;top:0;width:35%;height:2px;background:#1d2a2e}
.about-copy{position:absolute;left:7px;top:20px;width:390px}
.about-copy h2{margin-left:2px;margin-bottom:6px}
.about-copy p{font-family:Arimo,sans-serif;font-size:9.2px;line-height:14px;margin-top:16px}
.more{display:block;text-align:right;font-family:Arimo,sans-serif;font-size:9.5px;color:#fff;margin:5px 6px 0 0;text-decoration:underline}
.degrees{position:absolute;left:0;top:143px;width:398px;height:64px;background:var(--dark-panel);padding:5px 10px}
.degrees ul{list-style:none;display:grid;grid-template-columns:205px 178px;font-family:Arimo,sans-serif;font-size:8.3px;line-height:13.5px;margin-top:8px;white-space:nowrap}
.degrees li::before{content:"• "}
.video{position:absolute;left:413px;top:26px;width:192px}
.video h2{margin-left:2px;margin-bottom:6px}
.video-frame{margin-top:11px;height:146px;border:2px solid var(--blue);background:radial-gradient(circle at 50% 45%,#d7b79a 0 28%,#3f6b8a 55%,#3a5a3a 100%);position:relative}
.play{position:absolute;left:80px;top:62px}
.info{position:absolute;top:584px;left:0;width:612px;height:238px;background:var(--gray-panel)}
.col{position:absolute;top:28px}
.col h2{line-height:17px;height:38px}
.col svg.icon{position:absolute;right:0;top:2px}
.expert{left:11px;width:180px}
.portrait{position:absolute;left:11px;top:72px;width:68px;height:68px;border-radius:50%;border:2px solid #fff;background:linear-gradient(#d9c097,#4879a6)}
.expert-name{position:absolute;left:83px;top:82px;font-size:14px;line-height:16px}
.expert-name small{display:block;font-size:11px;margin-top:3px}
.checks{position:absolute;left:13px;top:140px;list-style:none;font-size:10px;line-height:13.7px;white-space:nowrap}
.checks li{display:flex;gap:3px;align-items:center}
.radio{left:210px;width:182px}
.quote-box{position:absolute;left:209px;top:77px;width:186px;height:111px;background:#dadcdc;border-radius:3px;color:#333;padding:7px 8px;font-family:Arimo,sans-serif;font-size:9.2px;line-height:13.9px}
.quote-box cite{display:block;text-align:right;font-style:normal;font-size:8px;color:#555}
.view-all{position:absolute;left:210px;top:194px;font-family:Arimo,sans-serif;font-size:9.5px;color:#fff;text-decoration:underline}
.inquiry{left:418px;width:185px}
.form{position:absolute;left:417px;top:78px;width:181px}
.field{height:20px;background:rgba(50,60,65,.65);margin-bottom:3px;font-family:Arimo,sans-serif;font-size:8px;padding:6px 7px;color:#ddd}
.field.msg{height:34px}
.submit{width:72px;height:20px;background:var(--blue);font-family:Arimo,sans-serif;font-weight:700;font-size:10px;display:flex;align-items:center;justify-content:center;margin-top:10px}
.reviews{position:absolute;top:822px;left:0;width:612px;height:191px;background:var(--reviews)}
.reviews h2{position:absolute;left:207px;top:27px;width:198px;text-align:center}
.reviews .title-line{position:absolute;left:207px;top:48px;width:198px}
.reviews .title-line::before{left:40%;width:20%;background:var(--blue)}
.patient{position:absolute;left:7px;top:59px;width:76px;height:76px;border-radius:50%;border:2px solid #fff;background:linear-gradient(#b99374,#242a33)}
.review-text{position:absolute;left:95px;top:63px;width:510px;font-family:Arimo,sans-serif;font-style:italic;font-size:8.6px;line-height:15.6px}
.review-by{position:absolute;left:96px;top:136px;font-family:Arimo,sans-serif;font-style:italic;font-weight:700;font-size:8.5px}
.read-testimonials{position:absolute;right:6px;top:149px;font-family:Arimo,sans-serif;font-size:8.5px;color:#fff;white-space:nowrap}
.read-testimonials u{text-decoration:underline}
.footer{position:absolute;top:1013px;left:0;width:612px;height:160px;background:var(--footer)}
.footer h3{font-weight:500;font-size:11px;margin-bottom:14px;white-space:nowrap}
.fcol{position:absolute;top:22px}
.links{list-style:none;font-family:Arimo,sans-serif;font-size:8.5px;line-height:14.5px}
.links .on{color:#c8a47a}
.donate{left:137px;width:170px}
.donate h3{border-bottom:1px dashed #777;padding-bottom:3px;margin-bottom:7px}
.badge{width:134px;height:52px;margin-bottom:3px;border:2px solid #9fc7e6}
.badge.one{background:#f4f4f4}
.badge.two{background:#8fa435}
.contact{left:323px;width:125px;font-family:Arimo,sans-serif;font-size:8.3px;line-height:12px}
.contact h3{font-family:"Barlow Semi Condensed",sans-serif;border-bottom:1px dashed #777;padding-bottom:3px;margin-bottom:11px}
.contact dl{display:grid;grid-template-columns:19px 1fr;row-gap:10px;white-space:nowrap}
.show{position:absolute;left:479px;top:1035px;width:123px;height:122px;background:linear-gradient(135deg,#d8337c 0 14%,#c9a58b 14% 60%,#4a6e8c 100%)}
.copyright{position:absolute;top:1173px;left:0;width:612px;height:27px;background:var(--blue);font-family:Arimo,sans-serif;font-size:8.5px;text-align:center;line-height:27px}
</style>
</head>
<body>
<div class="scene" role="img" aria-label="Beach backdrop with sky, turquoise sea and sand"></div>
<div class="page">
  <header class="header">
    <div class="brand">Dr. Mira L. Kalvoric</div>
    <div class="share"><i></i>Share</div>
    <div class="rating">Rivo</div>
    <div class="call">
      <svg viewBox="0 0 20 20"><circle cx="10" cy="10" r="9" fill="none" stroke="#fff" stroke-width="1.3"/><path d="M7 5c-1 1-1 3 1 6s4 4 5 4l1-1-2-2-1 1c-1-1-2-2-2-3l1-1-2-2z" fill="#fff"/></svg>
      <div><small>Call Us Today</small><b>555-201-4837</b></div>
    </div>
  </header>
  <nav class="nav">
    <a class="active">Home</a><a>About Me</a><a>Sessions</a><a>Resources</a><a>BIO</a><a>Customer Reviews</a><a style="border:0">Contact Us</a>
    <div class="follow">Follow Us On <span class="net"><i></i>Friendora</span><span class="net"><i class="chirp"></i>Chirpix</span></div>
  </nav>
  <section class="hero" role="img" aria-label="Sunrise over a golden wheat field">
    <h1>Committed To Assisting Our Clients To Overcome,<br>Achieve, And Improve Quality Of Life.</h1>
    <div class="arrow prev"><svg width="10" height="12"><path d="M7 1L2 6l5 5" stroke="#222" stroke-width="2" fill="none"/></svg></div>
    <div class="arrow next"><svg width="10" height="12"><path d="M3 1l5 5-5 5" stroke="#222" stroke-width="2" fill="none"/></svg></div>
  </section>
  <section class="about">
    <div class="about-copy">
      <h2>About Dr. Mira L. Kalvoric</h2>
      <div class="title-line" style="width:182px"></div>
      <p>While I acknowledge the importance of my education, I also appreciate the role my experiences have played in allowing me to relate so well to others. Allow me to share those I feel are most relevant with you.I survived an abusive childhood that my mother &amp; sister unfortunately did not. &amp; it was my grief &amp; desire to become stronger ...</p>
      <a class="more">Read More</a>
    </div>
    <div class="degrees">
      <h2>My Degrees</h2>
      <ul>
        <li>Doctoral Degree in Clinical Psychology</li><li>Doctoral Internship, Bayview Medical Center</li>
        <li>Masters Degree in Counseling Psychology</li><li>Masters Internship, Linden Clinic</li>
      </ul>
    </div>
    <div class="video">
      <h2>View Video</h2>
      <div class="title-line"></div>
      <div class="video-frame" role="img" aria-label="Video still of the psychologist">
        <svg class="play" width="20" height="20"><circle cx="10" cy="10" r="8.5" fill="none" stroke="#fff" stroke-width="1.5"/><path d="M8 6l6 4-6 4z" fill="#fff"/></svg>
      </div>
    </div>
  </section>
  <section class="info">
    <div class="col expert">
      <h2>My<br>Expertise</h2>
      <svg class="icon" width="28" height="30" viewBox="0 0 28 30"><path d="M14 2a12 12 0 0 0-11 15l3 4v7h10v-4h5l1-5 4-1-3-5A12 12 0 0 0 14 2z" fill="#ddd"/><circle cx="13" cy="13" r="4" fill="none" stroke="#777" stroke-width="2"/></svg>
      <div class="title-line"></div>
    </div>
    <div class="portrait" role="img" aria-label="Portrait of Dr. Kalvoric"></div>
    <div class="expert-name">Dr. Mira L.<br>Kalvoric<small>California # PSY20481</small></div>
    <ul class="checks">
      <li><svg width="9" height="8"><path d="M1 4l2.5 3L8 1" stroke="#fff" stroke-width="1.8" fill="none"/></svg>Dating, Marriage,</li>
      <li><svg width="9" height="8"><path d="M1 4l2.5 3L8 1" stroke="#fff" stroke-width="1.8" fill="none"/></svg>Parenting &amp; Professional Relationships</li>
      <li><svg width="9" height="8"><path d="M1 4l2.5 3L8 1" stroke="#fff" stroke-width="1.8" fill="none"/></svg>Depression &amp; Anxiety Issues</li>
      <li><svg width="9" height="8"><path d="M1 4l2.5 3L8 1" stroke="#fff" stroke-width="1.8" fill="none"/></svg>Personality Disorders</li>
      <li><svg width="9" height="8"><path d="M1 4l2.5 3L8 1" stroke="#fff" stroke-width="1.8" fill="none"/></svg>Life Management</li>
    </ul>
    <div class="col radio">
      <h2>Radio<br>Conversations</h2>
      <svg class="icon" width="20" height="30" viewBox="0 0 20 30"><rect x="5" y="1" width="10" height="17" rx="5" fill="#ddd"/><path d="M2 12a8 8 0 0 0 16 0M10 20v6M5 28h10" stroke="#ddd" stroke-width="2" fill="none"/></svg>
      <div class="title-line"></div>
    </div>
    <div class="quote-box"><b style="font-size:13px;color:#777">“</b> Lorem ipsum dolor sit ae onsectetuer adipiscing elit, sed diam nonummy nibh euis tincidunt ut laoreetlore gna aliquam erat olutpat. Ut wisi enim adinim veniam, quis strud xerci tation ullamrper suscipit lobortis sl ut al lorem.<cite>Anna Reyes</cite></div>
    <a class="view-all">View All</a>
    <div class="col inquiry">
      <h2>Quick<br>Inquiry</h2>
      <svg class="icon" width="38" height="28" viewBox="0 0 38 28"><rect x="1" y="1" width="36" height="26" fill="none" stroke="#eee" stroke-width="2"/><path d="M1 1l18 15L37 1M1 27l13-13M37 27L24 14" stroke="#eee" stroke-width="2" fill="none"/></svg>
      <div class="title-line"></div>
    </div>
    <div class="form">
      <div class="field">Name</div><div class="field">Email</div><div class="field">Phone</div><div class="field msg">Message</div>
      <div class="submit">SUBMIT</div>
    </div>
  </section>
  <section class="reviews">
    <h2>Reviews From Former Patients</h2>
    <div class="title-line"></div>
    <div class="patient" role="img" aria-label="Portrait of a former patient"></div>
    <p class="review-text"><b style="font-size:20px;color:#999;font-style:normal;line-height:0">“</b> Lorem ipsum dolor sit amet, consectetuer adipiscing elit, sed diam nonummy nibh euismod tincidunt ut laoreet dolore magna aliquam erat volutpat. Ut wisi enim ad minim veniam, quis nostrud exerci tation ullamcorper suscipit lobortis nisl ut aliquip commodo consequat. Duis autem vel eum iriure dolor in hendrerit in vulputate velit esse molestie consequat, vel illum dolore eu feugiat nulla facilisis at vero eros et accumsan et iusto odio dignissimaugue duis dolore te feugait nulla facilisi.</p>
    <div class="review-by">.... Lorem Ispum, Manger</div>
    <a class="read-testimonials"><u>Read more testimonials</u> »</a>
  </section>
  <footer class="footer">
    <div class="fcol" style="left:9px"><h3>Quick Links</h3>
      <ul class="links">
        <li class="on">Home</li><li>About Me</li><li>Sessions</li><li>Resources</li><li>BIO</li><li>Customer Reviews</li><li>Contact Me</li>
      </ul>
    </div>
    <div class="fcol donate"><h3>A Portion of All Revenue Is Donated To</h3>
      <div class="badge one" role="img" aria-label="Partner charity badge"></div>
      <div class="badge two" role="img" aria-label="Partner charity badge"></div>
    </div>
    <div class="fcol contact"><h3>Contact Details</h3>
      <dl>
        <dt>A:</dt><dd>410 Harbor Lane, Suite 120<br>Bayview, CA 90000</dd>
        <dt>P:</dt><dd>555-201-4837</dd>
        <dt>TF:</dt><dd>555-201-4837</dd>
        <dt>E:</dt><dd>mk@drkalvoric.com</dd>
      </dl>
    </div>
  </footer>
  <div class="show" role="img" aria-label="Silver Cedar Tunes radio show promo photo"></div>
  <div class="copyright">Copyright © 2016 Dr. Mira L. Kalvoric&nbsp; All rights reserved</div>
</div>
</body>
</html>
```